Website for Reiki and Wellness Courses

I teach online courses in Reiki and wellness/self-development and am needing a new website.

The focus of the website will be to provide descriptions of the courses as well as include a blog and pages where students in my courses will visit for additional information.

Note: courses are NOT hosted on this site.
The focus of this website will be to encourage viewers to enroll in courses as well as opt in to the email list.

I will upload copy soon. My old website is: http://brightfernstudies.example. Please do not use existing logo.

Target Market(s)

Alternative health, wellness, spirituality, personal development. Males and females of all ages seeking to improve their health and life.

Industry/Entity Type

Health And Wellness

Logo Text

No text (please do not use existing logo)

Coding

Coded - Design and coding required

Number of Pages Required

5+ page

Requirements
Must have
• 1. Home page
• 2. About page
• 3. Courses page that outlines courses (there are currently 6 courses with 1 coming soon)
• 4. Individual course page (maybe a template that I can adjust color and pictures for with each course)
• 5. Blog
• 6. Student Area that outlines all Student Areas
• 7. Individual Student Area page (maybe a template that I can adjust color and pictures for with each course)
• 8. Shop page (note: items will not currently be purchased through website - it will be a link to quillmarket for a book).
• 9. Student thank-you page (maybe a template that I can adjust color and pictures for with each course) this is the page students are directed to at end of course with vouchers for other courses.
• Opt-in for the home page, course pages, blog and thank-you pages
Nice to have
• I would like the design to be calm, clean and soothing. Ideally visitors feel relaxed when viewing the site and are encouraged to explore the courses, subscribe to the email list and purchase a product.
• ~ Testimonials page
• ~ Contact page
• I tend to gravitate towards blues, greys and purples as well as monochromatic color schemes.
Should not have
• Contact form on home page
• phone number on home page
• location/physical address
• dates for blog posts

```html
<!DOCTYPE html>
<html lang="en">
<head>
<meta charset="utf-8">
<title>Bright Fern Studies — Reiki &amp; Wellness Courses</title>
<link href="https://fonts.googleapis.com/css2?family=Raleway:wght@400;500;600;700&family=Open+Sans:ital,wght@0,400;0,600;0,700;1,400&display=swap" rel="stylesheet">
<style>
:root{
  --purple:#6f75a8;
  --purple-dark:#5d6296;
  --purple-light:#8a8fc2;
  --orange:#f0904a;
  --ink:#2f2f35;
  --text:#555860;
  --muted:#8a8c95;
  --soft:#f4f4f7;
  --white:#ffffff;
  --dark:#3b3838;
}
*{box-sizing:border-box;margin:0;padding:0}
html,body{width:1200px;height:2564px;overflow:hidden}
body{font-family:"Open Sans",Arial,sans-serif;color:var(--text);background:var(--white);position:relative}
.btn{position:absolute;display:flex;align-items:center;justify-content:center;color:var(--white);font-family:"Raleway",Arial,sans-serif;font-weight:700;letter-spacing:.5px;text-transform:uppercase}
.btn--orange{background:var(--orange)}
.btn--purple{background:var(--purple)}

/* header */
.site-header{position:absolute;top:0;left:0;width:1200px;height:79px;background:var(--white);border-top:3px solid var(--purple);box-shadow:0 1px 4px rgba(0,0,0,.08);z-index:5}
.brand{position:absolute;left:162px;top:22px;display:flex;align-items:center;gap:12px}
.brand__mark{width:30px;height:30px;background:var(--purple)}
.brand__name{font-family:"Raleway",Arial,sans-serif;font-size:22px;font-weight:600;color:var(--purple)}
.main-nav a{position:absolute;top:33px;font-family:"Raleway",Arial,sans-serif;font-size:12px;font-weight:600;color:var(--purple-dark);text-decoration:none;transform:translateX(-50%);letter-spacing:.3px}
.main-nav .is-active{color:var(--white);z-index:1;font-size:11px}
.nav-diamond{position:absolute;left:538px;top:17px;width:36px;height:36px;background:var(--purple);transform:rotate(45deg)}

/* hero */
.hero{position:absolute;top:79px;left:0;width:1200px;height:561px;overflow:hidden;background:var(--soft)}
.hero__photo{position:absolute;inset:0;background:
 radial-gradient(ellipse 380px 320px at 820px 280px,rgba(255,255,255,.85),rgba(255,255,255,0) 70%),
 radial-gradient(ellipse 500px 400px at 60px 80px,#ffffff,rgba(255,255,255,0) 70%),
 linear-gradient(180deg,#cfe4f6 0%,#e3eefa 55%,#f2f5fb 100%)}
.hero__title{position:absolute;left:162px;top:152px;font-family:"Raleway",Arial,sans-serif;font-size:31px;font-weight:600;line-height:40px;color:var(--purple)}
.hero__title span{color:var(--orange)}
.hero__text{position:absolute;left:162px;top:236px;width:420px;font-size:13px;line-height:20.5px;color:var(--text)}
.hero .btn{top:292px;height:39px;font-size:13px}
.hero__wave{position:absolute;left:0;top:361px}
.slider-dots{position:absolute;left:972px;top:497px;display:flex;gap:6px;z-index:2}
.slider-dots i{width:11px;height:11px;border-radius:50%;background:var(--white);display:block}
.slider-dots i.is-current{background:var(--purple)}

/* welcome */
.welcome{position:absolute;top:640px;left:0;width:1200px;height:252px;background:var(--soft)}
.section-title{position:absolute;left:0;width:1200px;display:flex;justify-content:center;align-items:center;gap:12px;font-family:"Raleway",Arial,sans-serif;font-size:24px;font-weight:500;color:var(--ink)}
.section-title .dot{width:22px;height:22px;border-radius:50%;background:var(--purple)}
.section-lead{position:absolute;left:210px;width:780px;text-align:center;font-size:10.5px;line-height:19.5px;color:var(--text)}

/* courses */
.courses{position:absolute;top:892px;left:0;width:1200px;height:470px;background:var(--white);border-top:1px solid #ececf0}
.card{position:absolute;top:137px;width:204px}
.card__image{width:204px;height:142px}
.card__title{margin-top:18px;font-family:"Raleway",Arial,sans-serif;font-size:14px;font-weight:600;color:var(--ink)}
.card__text{margin-top:11px;font-size:11px;line-height:19px;color:var(--text)}
.card .btn{position:relative;margin-top:14px;width:98px;height:34px;font-size:11px}

/* testimonials */
.testimonials{position:absolute;top:1362px;left:0;width:1200px;height:427px;overflow:hidden}
.testimonials__photo{position:absolute;inset:0;background:radial-gradient(ellipse 500px 300px at 300px 120px,#6b5a52,rgba(59,56,56,0) 70%),radial-gradient(ellipse 400px 300px at 950px 250px,#5c4f4a,rgba(59,56,56,0) 70%),var(--dark)}
.testimonials .section-title{top:52px;color:var(--white)}
.testimonials .section-title .dot{background:var(--purple-light)}
.quote{position:absolute;top:104px;width:277px;height:200px;padding:28px 24px 0 48px;font-size:12px;font-style:italic;line-height:20.5px;color:var(--white);background:var(--purple)}
.quote--featured{background:var(--orange)}
.quote::before{content:"\201C";position:absolute;left:14px;top:8px;font-family:Georgia,serif;font-size:60px;font-style:normal;line-height:60px;color:rgba(255,255,255,.35)}
.quote::after{content:"";position:absolute;left:22px;bottom:-16px;border-right:22px solid transparent;border-top:16px solid var(--purple)}
.quote--featured::after{border-top-color:var(--orange)}
.author{position:absolute;top:338px}
.author__name{font-family:"Raleway",Arial,sans-serif;font-size:15px;font-weight:600;color:var(--orange)}
.author__place{font-size:11px;color:#e4e4e8;margin-top:1px}

/* features */
.features{position:absolute;top:1789px;left:0;width:1200px;height:467px;background:var(--white)}
.feature{position:absolute;top:52px;width:273px}
.feature__title{font-family:"Raleway",Arial,sans-serif;font-size:22px;font-weight:500;color:var(--ink)}
.feature__image{margin-top:14px;width:273px;height:181px}
.feature__subtitle{margin-top:13px;font-family:"Raleway",Arial,sans-serif;font-size:14px;font-weight:700;color:var(--ink)}
.feature__text{margin-top:10px;font-size:11px;line-height:19px;color:var(--text)}
.feature .btn{position:relative;margin-top:16px;width:97px;height:33px;font-size:11px}

/* footer */
.site-footer{position:absolute;top:2256px;left:0;width:1200px;height:248px;background:linear-gradient(180deg,#7d83b8,#737aae);color:var(--white);border-top:3px solid var(--purple-dark)}
.footer-col{position:absolute;top:30px}
.footer-divider{position:absolute;top:0;width:1px;height:245px;background:rgba(255,255,255,.25)}
.footer-heading{font-family:"Raleway",Arial,sans-serif;font-size:13px;font-weight:700;letter-spacing:.5px;margin-bottom:20px}
.footer-links li{list-style:none;font-size:11px;line-height:23.3px}
.hours{border-collapse:collapse;font-size:11px}
.hours td{height:23.3px;padding:0}
.hours td:first-child{width:80px}
.contact-list li{list-style:none;display:flex;gap:12px;font-size:11px;line-height:20px}
.contact-list svg{flex:none;margin-top:6px}
.signup-field{width:177px;height:26px;margin-bottom:4px;padding:5px 8px;background:rgba(255,255,255,.22);font-size:10px;font-style:italic;color:var(--white)}
.signup-button{width:177px;height:30px;background:var(--orange);display:flex;align-items:center;justify-content:center;font-family:"Raleway",Arial,sans-serif;font-size:11px;font-weight:700;margin-top:6px}
.footer-bar{position:absolute;top:2504px;left:0;width:1200px;height:60px;background:var(--purple-dark);color:var(--white)}
.social{position:absolute;left:162px;top:18px;display:flex;gap:8px}
.social i{display:block;width:24px;height:24px;border-radius:50%;border:1.5px solid var(--white)}
.copyright{position:absolute;left:774px;top:22px;font-size:11px}
</style>
</head>
<body>

<header class="site-header">
  <div class="brand"><span class="brand__mark"></span><span class="brand__name">Bright Fern Studies</span></div>
  <div class="nav-diamond"></div>
  <nav class="main-nav">
    <a class="is-active" style="left:556px">HOME</a>
    <a style="left:638px">ABOUT</a>
    <a style="left:721px">COURSES</a>
    <a style="left:800px">BLOG</a>
    <a style="left:900px">STUDENT AREAS</a>
    <a style="left:1009px">CONTACT</a>
  </nav>
</header>

<section class="hero">
  <div class="hero__photo" role="img" aria-label="Woman meditating cross-legged in white clothing with colourful healing crystals floating above her hands against a bright sky"></div>
  <h1 class="hero__title">Reiki . . . the Sacred<br>way to your <span>Peaceful Heart</span></h1>
  <p class="hero__text">Sed ut perspiciatis unde omnis iste natuseor sitvoluptaccusan tiumdol orem qulanis iste natuseor sitvoluptaccusan tiu.</p>
  <a class="btn btn--purple" style="left:162px;width:151px">Join us free</a>
  <a class="btn btn--orange" style="left:319px;width:151px">Read more</a>
  <svg class="hero__wave" width="1200" height="200" viewBox="0 0 1200 200" aria-hidden="true">
    <path d="M0 115 C150 85 300 72 450 92 C650 120 750 180 880 182 C1000 184 1100 160 1200 138 L1200 200 L0 200 Z" fill="var(--purple)"/>
    <path d="M0 127 C150 97 300 84 450 104 C650 132 750 192 880 194 C1000 196 1100 172 1200 150 L1200 200 L0 200 Z" fill="var(--purple-light)"/>
    <path d="M0 132 C150 102 300 89 450 109 C650 137 750 197 880 199 C1000 201 1100 177 1200 155 L1200 200 L0 200 Z" fill="var(--soft)"/>
  </svg>
  <div class="slider-dots"><i></i><i></i><i class="is-current"></i><i></i></div>
</section>

<section class="welcome">
  <h2 class="section-title" style="top:16px">Welcome to <span class="dot"></span> Bright Fern Studies</h2>
  <p class="section-lead" style="top:70px">Lorem ipsum dolor sit amet, consectetur adipiscing elit, sed do eiusmod tempor incididunt ut labore et dolore mag na aliqua. Ut enim ad minim veniam, quis nostrud exercitation ullamco laboris nisi ut aliquip ex ea commodo consequatDuis aute irure dolor in reprehenderit in voluptate velit essem ipsum dolor sit amet, consectetur adipiscing elit, sed do eiusmod tempor incididunt ut labore et dolore mag na aliqua. Ut enim ad minim veniam, quis nostrud exe rcitation ullamco laboris nisi ut aliquip ex ea commodo consequuis aute irure dolor in reprehenderit in voluptate veliorem ipsum dolor sit amet.</p>
  <a class="btn btn--orange" style="left:552px;top:168px;width:97px;height:33px;font-size:11px">Read more</a>
</section>

<section class="courses">
  <h2 class="section-title" style="top:34px">Our <span class="dot"></span> Online Courses</h2>
  <p class="section-lead" style="top:80px">Lorem ipsum dolor sit amet, consectetur adipiscing elit, sed do eiusmod tempor incididunt ut labore et dolore magna aliqua. Ut enim ad minim veniam, quis nostrud exercitation ullamco laboris nisi ut aliquip ex ea commodo consequat. Duis aute irure dolor in reprehenderit in voluptate velit ess</p>
  <article class="card" style="left:162px">
    <div class="card__image" role="img" aria-label="Two open hands with glowing pink and white light between them" style="background:linear-gradient(135deg,#f3c7c9,#e9d7ef 50%,#f6e6dc)"></div>
    <h3 class="card__title">Finibus Bonorum et Malorum</h3>
    <p class="card__text">Sed ut perspiciatis unde omnis iste nats error sit voluptatem accusantium dolore mque laudantium, totam rem.</p>
    <a class="btn btn--orange">Read more</a>
  </article>
  <article class="card" style="left:386px">
    <div class="card__image" role="img" aria-label="Woman lying relaxed while receiving a head treatment in soft blue light" style="background:linear-gradient(135deg,#b9dcf2,#e7f1f8 55%,#d8c9bd)"></div>
    <h3 class="card__title">Finibus Bonorum et Malorum</h3>
    <p class="card__text">Sed ut perspiciatis unde omnis iste nats error sit voluptatem accusantium dolore mque laudantium, totam rem.</p>
    <a class="btn btn--purple">Read more</a>
  </article>
  <article class="card" style="left:610px">
    <div class="card__image" role="img" aria-label="Woman in white raising her arms toward a deep blue evening sea" style="background:linear-gradient(180deg,#33467a,#7a90bd 55%,#2c3b62)"></div>
    <h3 class="card__title">Finibus Bonorum et Malorum</h3>
    <p class="card__text">Sed ut perspiciatis unde omnis iste nats error sit voluptatem accusantium dolore mque laudantium, totam rem.</p>
    <a class="btn btn--purple">Read more</a>
  </article>
  <article class="card" style="left:834px">
    <div class="card__image" role="img" aria-label="Practitioner giving a Reiki session to a woman lying on a treatment table" style="background:linear-gradient(135deg,#6a4b4b,#c89a8a 50%,#efe3dc)"></div>
    <h3 class="card__title">Finibus Bonorum et Malorum</h3>
    <p class="card__text">Sed ut perspiciatis unde omnis iste nats error sit voluptatem accusantium dolore mque laudantium, totam rem.</p>
    <a class="btn btn--purple">Read more</a>
  </article>
</section>

<section class="testimonials">
  <div class="testimonials__photo" role="img" aria-label="Darkened close view of hands resting gently on a relaxed client's head"></div>
  <h2 class="section-title">Satisfied Customers, <span class="dot"></span> Have a Say!</h2>
  <blockquote class="quote" style="left:162px">Sed ut perspiciatis unde omnis iste nater ror sit voptamaccusantiumlord olo rque laudantium, totam rem erid persloypiciatis unde omnis iste nater ror sit voluptatem accs antium dolor que laudantium, totam rem operiam edut perspiciatis unde.</blockquote>
  <blockquote class="quote quote--featured" style="left:461px">Sed ut perspiciatis unde omnis iste nater ror sit voptamaccusantiumlord olo rque laudantium, totam rem erid persloypiciatis unde omnis iste nater ror sit voluptatem accs antium dolor que laudantium, totam rem operiam edut perspiciatis unde.</blockquote>
  <blockquote class="quote" style="left:760px">Sed ut perspiciatis unde omnis iste nater ror sit voptamaccusantiumlord olo rque laudantium, totam rem erid persloypiciatis unde omnis iste nater ror sit voluptatem accs antium dolor que laudantium, totam rem operiam edut perspiciatis unde.</blockquote>
  <div class="author" style="left:162px"><div class="author__name">Milo Harten</div><div class="author__place">Male from United States</div></div>
  <div class="author" style="left:461px"><div class="author__name">Milo Harten</div><div class="author__place">Male from United States</div></div>
  <div class="author" style="left:760px"><div class="author__name">Milo Harten</div><div class="author__place">Male from United States</div></div>
</section>

<section class="features">
  <article class="feature" style="left:162px">
    <h2 class="feature__title">How Reiki Works</h2>
    <div class="feature__image" role="img" aria-label="Hands hovering above a woman resting on a towel during a healing session" style="background:linear-gradient(135deg,#f4eee9,#e2cbb8 55%,#b89a84)"></div>
    <h3 class="feature__subtitle">Finibus Bonorum et Mlorem ipsorum</h3>
    <p class="feature__text">Sed ut perspiciatis unde omnis iste nats error sit vol uptatem accusantium dolore mque laudantium, totam ratem accusantium dolore em.</p>
    <a class="btn btn--orange">Read more</a>
  </article>
  <article class="feature" style="left:461px">
    <h2 class="feature__title">Master Certification</h2>
    <div class="feature__image" role="img" aria-label="Silhouette of a person raising an arm against a golden sunset over the sea" style="background:linear-gradient(180deg,#f0b45a,#c9783a 50%,#3a2a22)"></div>
    <h3 class="feature__subtitle">Finibus Bonorum et Mlorem ipsorum</h3>
    <p class="feature__text">Sed ut perspiciatis unde omnis iste nats error sit vol uptatem accusantium dolore mque laudantium, totam ratem accusantium dolore em.</p>
    <a class="btn btn--purple">Read more</a>
  </article>
  <article class="feature" style="left:763px">
    <h2 class="feature__title">Resources</h2>
    <div class="feature__image" role="img" aria-label="Hands placed softly on the head of a relaxed client" style="background:linear-gradient(135deg,#5a3f38,#c69380 55%,#e8c8b6)"></div>
    <h3 class="feature__subtitle">Finibus Bonorum et Mlorem ipsorum</h3>
    <p class="feature__text">Sed ut perspiciatis unde omnis iste nats error sit vol uptatem accusantium dolore mque laudantium, totam ratem accusantium dolore em.</p>
    <a class="btn btn--purple">Read more</a>
  </article>
</section>

<footer class="site-footer">
  <span class="footer-divider" style="left:270px"></span>
  <span class="footer-divider" style="left:547px"></span>
  <span class="footer-divider" style="left:815px"></span>
  <div class="footer-col" style="left:162px">
    <h4 class="footer-heading">LINKS</h4>
    <ul class="footer-links"><li>Home</li><li>About</li><li>Courses</li><li>Blog</li><li>Student Areas</li><li>Contact</li></ul>
  </div>
  <div class="footer-col" style="left:325px">
    <h4 class="footer-heading">OPENING HOURS</h4>
    <table class="hours">
      <tr><td>Monday</td><td>9:00am - 5:00pm</td></tr>
      <tr><td>Tuesday</td><td>9:00am - 5:00pm</td></tr>
      <tr><td>Wednesday</td><td>9:00am - 5:00pm</td></tr>
      <tr><td>Thursday</td><td>9:00am - 5:00pm</td></tr>
      <tr><td>Friday</td><td>9:00am - 5:00pm</td></tr>
      <tr><td>Sat &amp; Sunday</td><td>CLOSED</td></tr>
    </table>
  </div>
  <div class="footer-col" style="left:600px">
    <h4 class="footer-heading">CONTACT US</h4>
    <ul class="contact-list">
      <li><svg width="11" height="8" viewBox="0 0 11 8"><rect x=".5" y=".5" width="10" height="7" fill="#fff"/><path d="M.5 .5 L5.5 4.5 L10.5 .5" fill="none" stroke="#7b80b5"/></svg><span>Email: info@brightfernstudies.example</span></li>
    </ul>
  </div>
  <div class="footer-col" style="left:860px">
    <h4 class="footer-heading">STAY INSPIRED</h4>
    <div class="signup-field">Name:</div>
    <div class="signup-field">Email:</div>
    <div class="signup-button">YES-COUNT ME IN</div>
  </div>
</footer>

<div class="footer-bar">
  <div class="social"><i></i><i></i><i></i><i></i></div>
  <p class="copyright">© 2016 brightfernstudies.example. All Copyrights are Reserved.</p>
</div>

</body>
</html>
```